Business card for Sports Apparel business

DOUBLE SIDED DESIGN
We need business cards for a new sports apparel business. We are developing a protective headband for soccer initially.
Torvalle is focused on designing and developing head protection products to reduce the likelihood of concussion when playing sports. Exploring and understanding medical insights, material science research, current and former players experiences and governing bodies guidelines has allowed Torvalle to develop the safety, style, form and function requirements of a suitable product to bring to market.
Target Market(s)
Mums buying kits for the sons and daughters. Amateur footballers.
Industry/Entity Type
Sporting Good
Contact Information for Business Card
Martin Ashworth - CEO
Mobile: +44 7431589027
Email: martin@torvalle.co.uk
Tel: 0208 5519372
Helena Pargeter - COO
Mob: +44 7385 640117
Email: helena@torvalle.co.uk
Tel: 0208 5519372
Duncan Farrow - CCO
Mob: +44 7564 293081
Email: duncan@torvalle.co.uk
Tel: 0208 5519372
Look and feel
Each slider illustrates characteristics of the customer's brand and the style your logo design should communicate.

```html
<!DOCTYPE html>
<html lang="en">
<head>
<meta charset="utf-8">
<title>Torvalle Business Card</title>
<link rel="stylesheet" href="https://fonts.googleapis.com/css2?family=Montserrat:wght@400;500;600;700&display=swap">
<style>
  :root {
    --backdrop: #2e2a28;
    --card-blue: #1f69a3;
    --card-blue-deep: #1a5c91;
    --ink-white: #ffffff;
    --ink-soft: rgba(255,255,255,0.92);
  }
  * { margin: 0; padding: 0; box-sizing: border-box; }
  html, body { width: 1200px; height: 716px; overflow: hidden; }
  body {
    background: var(--backdrop);
    font-family: "Montserrat", sans-serif;
    position: relative;
  }
  .card {
    position: absolute;
    top: 208px;
    width: 525px;
    height: 300px;
    background: linear-gradient(135deg, var(--card-blue) 0%, var(--card-blue-deep) 100%);
    border-radius: 4px;
    box-shadow: 0 10px 28px rgba(0,0,0,0.45);
    color: var(--ink-white);
  }
  .card-front { left: 50px; }
  .card-back { left: 625px; }

  .wordmark {
    font-weight: 700;
    text-transform: uppercase;
    color: var(--ink-white);
    letter-spacing: 0.06em;
    line-height: 1;
  }
  .card-front .wordmark {
    position: absolute;
    left: 0; right: 0; top: 50%;
    transform: translateY(-50%);
    text-align: center;
    font-size: 46px;
  }
  .card-back .wordmark {
    position: absolute;
    left: 40px;
    top: 122px;
    font-size: 30px;
  }
  .divider {
    position: absolute;
    left: 268px;
    top: 92px;
    width: 1px;
    height: 138px;
    background: var(--ink-soft);
  }
  .contact-block {
    position: absolute;
    left: 292px;
    top: 98px;
  }
  .person-name {
    font-weight: 600;
    font-size: 15px;
    letter-spacing: 0.08em;
    text-transform: uppercase;
  }
  .person-role {
    font-weight: 400;
    font-size: 11px;
    letter-spacing: 0.06em;
    margin-top: 3px;
  }
  .contact-list {
    list-style: none;
    margin-top: 16px;
  }
  .contact-list li {
    display: flex;
    align-items: center;
    gap: 8px;
    font-size: 11.5px;
    font-weight: 400;
    letter-spacing: 0.03em;
    line-height: 1;
    margin-bottom: 8px;
  }
  .contact-list svg {
    width: 11px;
    height: 11px;
    flex: none;
    fill: none;
    stroke: var(--ink-white);
    stroke-width: 1.4;
  }
</style>
</head>
<body>
  <section class="card card-front" aria-label="Card front">
    <div class="wordmark">Torvalle</div>
  </section>

  <section class="card card-back" aria-label="Card back">
    <div class="wordmark">Torvalle</div>
    <div class="divider"></div>
    <div class="contact-block">
      <div class="person-name">Martin Ashworth</div>
      <div class="person-role">CEO</div>
      <ul class="contact-list">
        <li>
          <svg viewBox="0 0 12 12" aria-hidden="true"><path d="M3 1.5 L4.6 1.5 L5.2 4 L4 4.8 Q5 7 7.2 8 L8 6.8 L10.5 7.4 L10.5 9 Q10.5 10.5 9 10.5 Q1.5 10 1.5 3 Q1.5 1.5 3 1.5 Z"/></svg>
          <span>0208 5519372</span>
        </li>
        <li>
          <svg viewBox="0 0 12 12" aria-hidden="true"><rect x="3" y="0.8" width="6" height="10.4" rx="1"/><line x1="5.3" y1="9.3" x2="6.7" y2="9.3"/></svg>
          <span>+44 7431589027</span>
        </li>
        <li>
          <svg viewBox="0 0 12 12" aria-hidden="true"><rect x="1" y="2.5" width="10" height="7" rx="0.6"/><path d="M1 3 L6 6.8 L11 3"/></svg>
          <span>martin@torvalle.co.uk</span>
        </li>
        <li>
          <svg viewBox="0 0 12 12" aria-hidden="true"><circle cx="6" cy="6" r="5"/><ellipse cx="6" cy="6" rx="2.2" ry="5"/><line x1="1" y1="6" x2="11" y2="6"/></svg>
          <span>www.torvalle.co.uk</span>
        </li>
      </ul>
    </div>
  </section>
</body>
</html>
```